Tidewell Homecare

I am looking to have a website designed for a housekeeping company that looks similar to this one. https://marloweshomecare.example/

I need 5 websites designed but will start with this one to see how I like it.

Industry/Entity Type

House Cleaning

Coding

Coded - Design and coding required

Number of Pages Required

5+ page

Font styles to use
Serif
Script

Colors
ffffff
fdf9cf
fbf289
fbee3f
d6edf3
86cae7
33a6d7
edf1f8
cedeed

```html
<!DOCTYPE html>
<html lang="en">
<head>
<meta charset="utf-8">
<title>Tidewell Homecare</title>
<link rel="stylesheet" href="https://fonts.googleapis.com/css2?family=Roboto:ital,wght@0,400;0,500;0,700;0,900;1,400&display=swap">
<style>
:root{
  --white:#ffffff;
  --blue:#33a6d7;
  --blue-deep:#2b93d0;
  --blue-soft:#86cae7;
  --sky:#d6edf3;
  --mist:#edf1f8;
  --steel:#cedeed;
  --yellow:#fbee3f;
  --yellow-soft:#fbf289;
  --cream:#fdf9cf;
  --ink:#1d1d1d;
  --text:#555555;
  --footer:#1e1f21;
}
*{box-sizing:border-box;margin:0;padding:0}
html,body{width:1200px;height:3840px;overflow:hidden}
body{position:relative;font-family:'Roboto',sans-serif;color:var(--ink);background:var(--white)}
.abs{position:absolute}
.btn{position:absolute;display:flex;align-items:center;justify-content:center;gap:8px;background:var(--yellow);color:#1a1a1a;font-weight:700;font-size:16px;border-radius:3px;text-transform:uppercase}
.btn svg{width:15px;height:15px}

/* header */
.topline{left:0;top:0;width:1200px;height:5px;background:var(--blue-deep)}
.site-header{left:0;top:5px;width:1200px;height:89px;background:var(--white)}
.brand{display:flex;align-items:center;gap:12px}
.brand-dot{width:46px;height:46px;border-radius:50%;background:var(--yellow)}
.brand-name{font-weight:700;font-size:17px;line-height:22px;text-transform:uppercase;color:var(--ink)}
.site-header .brand{position:absolute;left:112px;top:20px}
.nav{position:absolute;left:408px;top:34px;display:flex;gap:20px;font-size:15px;font-weight:500}
.nav .active{color:var(--blue-deep);position:relative}
.nav .active:after{content:"";position:absolute;left:0;right:0;top:25px;height:3px;background:var(--blue-deep)}
.call{left:778px;top:28px;width:150px;height:42px;font-size:15px;text-transform:none}
.estimate{position:absolute;left:943px;top:27px;width:146px;height:44px;border:2px solid var(--blue-deep);border-radius:3px;color:var(--blue-deep);font-weight:700;font-size:15px;display:flex;align-items:center;justify-content:center}

/* hero */
.hero{left:0;top:94px;width:1200px;height:594px;z-index:2;clip-path:polygon(0 0,100% 0,100% 532px,49.4% 594px,0 535px);
  background:linear-gradient(180deg,#cfc6b4 0%,#8d7c64 40%,#3d3228 80%,#2b241e 100%)}
.hero-box{left:432px;top:152px;width:430px;height:142px;background:rgba(60,60,60,.55)}
.hero h1{position:absolute;left:0;top:178px;width:1200px;text-align:center;color:var(--white);font-size:33px;font-weight:900;letter-spacing:.5px}
.hero p{position:absolute;left:350px;top:236px;width:500px;text-align:center;color:var(--white);font-size:16px;font-weight:500;line-height:26px}
.hero .btn{left:512px;top:318px;width:176px;height:51px}
.slide-arrow{position:absolute;top:254px;width:40px;height:40px;border:2px solid rgba(255,255,255,.8);border-radius:50%;display:flex;align-items:center;justify-content:center}
.slide-arrow svg{width:14px;height:14px}

/* services */
.service{top:626px;height:575px;width:600px;text-align:center}
.service.res{left:0;background:linear-gradient(160deg,#3aa5dc,#2c8fcf);color:var(--white)}
.service.com{left:593px;width:607px;background:linear-gradient(160deg,#f5f6f8,#e4e8ee);color:var(--ink)}
.service svg.icon{position:absolute;top:162px;width:76px;height:76px}
.service h2{position:absolute;top:262px;left:0;right:0;font-size:26px;font-weight:700;letter-spacing:.5px}
.service p{position:absolute;top:308px;left:70px;right:70px;font-size:15px;line-height:26px}
.service.com p{color:var(--text)}
.service .btn{top:412px;height:48px;font-size:15px}

/* welcome */
.welcome h2{position:absolute;left:0;top:1320px;width:1200px;text-align:center;font-size:35px;font-weight:700}
.welcome p{position:absolute;left:145px;top:1388px;width:910px;text-align:center;font-size:15px;line-height:28px;color:var(--text)}
.field{position:absolute;width:216px;height:37px;border:1px solid #cfd6de;border-radius:3px;background:#fafbfc;font-size:13px;color:#666;padding:0 12px;display:flex;align-items:center;justify-content:space-between;box-shadow:0 1px 2px rgba(0,0,0,.08)}
.field svg{width:14px;height:14px}
.welcome .btn{left:524px;top:1658px;width:152px;height:50px}

/* hard work */
.work-photo{left:0;top:1833px;width:600px;height:460px;background:linear-gradient(135deg,#e7ebef,#c3ccd4 50%,#8f9aa5)}
.work-panel{left:600px;top:1833px;width:600px;height:460px;background:var(--blue-deep);color:var(--white)}
.work-panel h2{position:absolute;left:63px;top:66px;font-size:35px;font-weight:700}
.work-panel p{position:absolute;left:66px;top:130px;width:423px;font-size:15px;line-height:26px;text-align:justify}
.work-panel .btn{left:66px;top:340px;width:194px;height:48px;font-size:15px}

/* why us */
.why h2{position:absolute;left:0;top:2408px;width:1200px;text-align:center;font-size:35px;font-weight:700}
.card{position:absolute;width:458px;height:156px;background:var(--white);box-shadow:0 1px 6px rgba(0,0,0,.14)}
.card .ico{position:absolute;left:0;top:6px;width:133px;height:144px;border-right:1px solid #e2e2e2;display:flex;align-items:center;justify-content:center}
.card .ico svg{width:62px;height:62px}
.card h3{position:absolute;left:160px;top:26px;font-size:19px;font-weight:500}
.card p{position:absolute;left:160px;top:60px;width:280px;font-size:14px;line-height:24px;color:var(--text)}

/* testimonials */
.reviews{left:0;top:2985px;width:1200px;height:418px;background:linear-gradient(180deg,#2d7fe0 0%,#3d8ff0 55%,#4aa0ee 100%);overflow:hidden}
.reviews .props{position:absolute;left:0;bottom:0;width:1200px;height:150px;background:linear-gradient(90deg,#c7e23a,#e94a3a 30%,#38c06a 50%,#3b7be3 70%,#e0443a 88%,#f2e44a)}
.reviews h2{position:absolute;left:0;top:56px;width:1200px;text-align:center;color:var(--white);font-size:34px;font-weight:900;letter-spacing:-.3px}
.avatar{left:190px;top:140px;width:96px;height:96px;border-radius:50%;background:linear-gradient(135deg,#cfd8e4,#6f8fb3);border:3px solid var(--white)}
.quote-mark{position:absolute;font-size:54px;font-weight:900;color:var(--yellow);line-height:1}
.reviews blockquote{position:absolute;left:322px;top:135px;width:672px;color:var(--white);font-style:italic;font-size:15.5px;line-height:27px}
.reviews .who{position:absolute;left:322px;top:227px;color:var(--white)}
.reviews .who b{display:block;font-size:17px;font-weight:500}
.reviews .who span{font-size:12px}
.rev-arrow{position:absolute;top:166px;width:30px;height:44px}

/* footer */
.site-footer{left:0;top:3403px;width:1200px;height:437px;background:var(--footer);color:var(--white)}
.site-footer .brand{position:absolute;left:144px;top:142px}
.site-footer .brand-name{color:var(--white)}
.socials{position:absolute;left:138px;top:246px;display:flex;gap:24px}
.socials span{width:22px;height:22px;border-radius:50%;background:var(--white)}
.vline{position:absolute;top:146px;width:1px;height:150px;background:#3a3b3e}
.site-footer h4{position:absolute;top:104px;font-size:18px;font-weight:500;letter-spacing:.3px}
.contact-row{position:absolute;left:471px;display:flex;gap:16px;font-size:14px;line-height:20px}
.contact-row svg{width:16px;height:16px;flex:none;margin-top:2px}
.news-text{position:absolute;left:818px;top:160px;width:270px;font-size:12px;line-height:20px}
.news-input{position:absolute;left:818px;top:212px;width:273px;height:34px;background:var(--white);border-radius:2px;color:#444;font-size:12px;padding:0 16px;display:flex;align-items:center}
.news-btn{position:absolute;left:818px;top:258px;width:102px;height:38px;background:var(--blue-deep);border-radius:2px;font-size:13px;font-weight:700;display:flex;align-items:center;justify-content:center}
.footer-rule{position:absolute;left:115px;top:332px;width:978px;height:1px;background:#55565a}
.copyright{position:absolute;left:0;top:360px;width:1200px;text-align:center;font-size:13px}
</style>
</head>
<body>

<div class="abs topline"></div>
<header class="abs site-header">
  <div class="brand"><span class="brand-dot"></span><span class="brand-name">Tidewell<br>Homecare</span></div>
  <nav class="nav"><span class="active">Home</span><span>Services</span><span>Gift Cards</span><span>About</span><span>Contact</span></nav>
  <div class="btn call"><svg viewBox="0 0 24 24"><path fill="#1a1a1a" d="M6.6 10.8a15 15 0 006.6 6.6l2.2-2.2c.3-.3.7-.4 1-.2 1.1.4 2.3.6 3.6.6.6 0 1 .4 1 1V20c0 .6-.4 1-1 1A17 17 0 013 4c0-.6.4-1 1-1h3.5c.6 0 1 .4 1 1 0 1.3.2 2.5.6 3.6.1.3 0 .7-.2 1z"/></svg>555 014 2290</div>
  <div class="estimate">FREE ESTIMATE</div>
</header>

<section class="abs hero" role="img" aria-label="Bright modern kitchen with dark countertops and wooden stairs">
  <div class="abs hero-box"></div>
  <h1>TIDEWELL HOMECARE</h1>
  <p>Lorem ipsum dolor sit amet, consectetur adipiscing elit, sed do eiusmod tempor incididunt ut labore magna aliqua.</p>
  <div class="btn">Get Started <svg viewBox="0 0 16 16"><circle cx="8" cy="8" r="8" fill="#1a1a1a"/><path d="M6 4.5L9.5 8 6 11.5" stroke="#fbee3f" stroke-width="2" fill="none"/></svg></div>
  <div class="slide-arrow" style="left:33px"><svg viewBox="0 0 14 14"><path d="M9 2L4 7l5 5" stroke="#fff" stroke-width="1.6" fill="none"/></svg></div>
  <div class="slide-arrow" style="left:1129px"><svg viewBox="0 0 14 14"><path d="M5 2l5 5-5 5" stroke="#fff" stroke-width="1.6" fill="none"/></svg></div>
</section>

<section class="abs service res">
  <svg class="icon" style="left:252px" viewBox="0 0 76 76" fill="none" stroke="#fff" stroke-width="3"><path d="M6 36L38 8l32 28"/><path d="M14 30v38h48V30"/><rect x="22" y="42" width="12" height="12"/><rect x="42" y="46" width="12" height="22"/><path d="M50 14h8v12"/></svg>
  <h2>RESIDENTIAL CLEANING</h2>
  <p>Lorem ipsum dolor sit amet, consectetur adipiscing elit, sed do eiusmod tempor incididunt ut labore et dolore magna aliqua. Ut enim ad minim veniam, quis nostrud exercitation</p>
  <div class="btn" style="left:175px;width:232px">Residential Services <svg viewBox="0 0 16 16"><circle cx="8" cy="8" r="8" fill="#1a1a1a"/><path d="M6 4.5L9.5 8 6 11.5" stroke="#fbee3f" stroke-width="2" fill="none"/></svg></div>
</section>

<section class="abs service com">
  <svg class="icon" style="left:273px" viewBox="0 0 76 76" fill="none" stroke="#2b93d0" stroke-width="3"><rect x="12" y="10" width="40" height="58"/><path d="M52 30h14v38H52M4 68h68"/><path d="M20 20h6M34 20h6M20 32h6M34 32h6M20 44h6M34 44h6M58 40h4M58 52h4"/><rect x="26" y="54" width="12" height="14"/></svg>
  <h2>COMMERCIAL/OFFICE CLEANING</h2>
  <p>Lorem ipsum dolor sit amet, consectetur adipiscing elit, sed do eiusmod tempor incididunt ut labore et dolore magna aliqua. Ut enim ad minim veniam, quis nostrud exercitation</p>
  <div class="btn" style="left:193px;width:230px">Commercial Services <svg viewBox="0 0 16 16"><circle cx="8" cy="8" r="8" fill="#1a1a1a"/><path d="M6 4.5L9.5 8 6 11.5" stroke="#fbee3f" stroke-width="2" fill="none"/></svg></div>
</section>

<section class="welcome">
  <h2>Welcome To Tidewell Homecare</h2>
  <p>Sed ut perspiciatis unde omnis iste natus error sit voluptatem accusantium doloremque laudantium, totam rem aperiam, eaque ipsa quae ab illo inventore veritatis et quasi architecto beatae vitae dicta sunt explicabo. Nemo enim ipsam voluptatem quia voluptas sit aspernatur aut odit aut fugit, sed quia consequuntur magni dolores eos qui ratione voluptatem sequi nesciunt.</p>
  <div class="field" style="left:128px;top:1517px">Name*<svg viewBox="0 0 14 14"><path d="M2 12l1-3 7-7 2 2-7 7z" fill="#2b93d0"/></svg></div>
  <div class="field" style="left:370px;top:1517px">Email*<svg viewBox="0 0 14 14"><rect x="1" y="3" width="12" height="9" fill="#2b93d0"/><path d="M1 3l6 5 6-5" stroke="#fff" fill="none"/></svg></div>
  <div class="field" style="left:612px;top:1517px">City*<svg viewBox="0 0 14 14"><path d="M7 1a4 4 0 014 4c0 3-4 8-4 8S3 8 3 5a4 4 0 014-4z" fill="#2b93d0"/><circle cx="7" cy="5" r="1.5" fill="#fff"/></svg></div>
  <div class="field" style="left:854px;top:1517px">Square Footage*<svg viewBox="0 0 14 14" fill="none" stroke="#2b93d0" stroke-width="1.5"><path d="M1 4V1h3M10 1h3v3M13 10v3h-3M4 13H1v-3"/></svg></div>
  <div class="field" style="left:128px;top:1575px">House<svg viewBox="0 0 14 14"><path d="M3 5h8L7 10z" fill="#2b93d0"/></svg></div>
  <div class="field" style="left:370px;top:1575px">Type of Cleaning*<svg viewBox="0 0 14 14"><path d="M3 5h8L7 10z" fill="#2b93d0"/></svg></div>
  <div class="field" style="left:612px;top:1575px">Frequency*<svg viewBox="0 0 14 14"><path d="M3 5h8L7 10z" fill="#2b93d0"/></svg></div>
  <div class="field" style="left:854px;top:1575px">mm/dd/yyyy<svg viewBox="0 0 14 14"><rect x="1" y="2" width="12" height="11" fill="#2b93d0"/><path d="M2 5h10M4 7h2M8 7h2M4 10h2M8 10h2" stroke="#fff"/></svg></div>
  <div class="btn">Submit <svg viewBox="0 0 16 16"><circle cx="8" cy="8" r="8" fill="#1a1a1a"/><path d="M6 4.5L9.5 8 6 11.5" stroke="#fbee3f" stroke-width="2" fill="none"/></svg></div>
</section>

<div class="abs work-photo" role="img" aria-label="Cleaning crew vacuuming and wiping desks in a bright office"></div>
<section class="abs work-panel">
  <h2>Hard Work &amp; Reliability</h2>
  <p>Sed ut perspiciatis unde omnis iste natus error sit voluptatem accusantium doloremque laudantium, totam rem aperiam, eaque ipsa quae ab illo inventore veritatis et quasi architecto beatae vitae dicta sunt explicabo. Nemo ipsam voluptatem quia voluptas sit aspernatur aut odit aut fugit, consequuntur magni dolores eos qui ratione voluptatem sequi nesciunt. Neque porro quisquam est,</p>
  <div class="btn">Get To Know Us <svg viewBox="0 0 16 16"><circle cx="8" cy="8" r="8" fill="#1a1a1a"/><path d="M6 4.5L9.5 8 6 11.5" stroke="#fbee3f" stroke-width="2" fill="none"/></svg></div>
</section>

<section class="why">
  <h2>Why Us Tidewell Homecare</h2>
  <div class="card" style="left:112px;top:2499px">
    <div class="ico"><svg viewBox="0 0 62 62" fill="none" stroke="#2b93d0" stroke-width="2"><rect x="12" y="8" width="34" height="46"/><circle cx="26" cy="22" r="5"/><path d="M18 34c2-5 14-5 16 0M18 40h22M18 46h22"/><circle cx="46" cy="20" r="6"/></svg></div>
    <h3>Experienced</h3>
    <p>Sed ut perspiciatis unde omnis iste natus error voluptatem accusantium doloremque laudantium, totam rem aperiam,</p>
  </div>
  <div class="card" style="left:626px;top:2499px">
    <div class="ico"><svg viewBox="0 0 62 62" fill="none" stroke="#2b93d0" stroke-width="2"><path d="M26 8l18 7v12c0 12-8 20-18 24C16 47 8 39 8 27V15z"/><path d="M18 24h16M18 30h12"/><path d="M40 36v14h10V40l-4-6"/></svg></div>
    <h3>Reliable</h3>
    <p>Sed ut perspiciatis unde omnis iste natus error voluptatem accusantium doloremque laudantium, totam rem aperiam,</p>
  </div>
  <div class="card" style="left:112px;top:2696px">
    <div class="ico"><svg viewBox="0 0 62 62" fill="none" stroke="#2b93d0" stroke-width="2"><path d="M14 50l-4-18V14a3 3 0 016 0v12M16 12a3 3 0 016 0v14M22 10a3 3 0 016 0v16M28 14a3 3 0 016 0v18l-8 18"/><path d="M34 40l8-10 6-4a3 3 0 014 4l-8 10-8 12"/></svg></div>
    <h3>Convenient</h3>
    <p>Sed ut perspiciatis unde omnis iste natus error voluptatem accusantium doloremque laudantium, totam rem aperiam,</p>
  </div>
  <div class="card" style="left:626px;top:2696px">
    <div class="ico"><svg viewBox="0 0 62 62" fill="none" stroke="#2b93d0" stroke-width="2"><path d="M31 6v50M31 6l-6 6M31 6l6 6M8 28h46M8 28l6-6M8 28l6 6M54 28l-6-6M54 28l-6 6"/><circle cx="31" cy="28" r="7"/></svg></div>
    <h3>Flexible</h3>
    <p>Sed ut perspiciatis unde omnis iste natus error voluptatem accusantium doloremque laudantium, totam rem aperiam,</p>
  </div>
</section>

<section class="abs reviews">
  <div class="props" role="img" aria-label="Colourful cleaning supplies: gloves, sponges, spray bottles and cloths"></div>
  <h2>WHAT OUR CLIENTS HAVE TO SAY</h2>
  <svg class="rev-arrow" style="left:106px" viewBox="0 0 30 44"><path d="M22 4L6 22l16 18" stroke="#fff" stroke-width="4" fill="none"/></svg>
  <svg class="rev-arrow" style="left:1063px" viewBox="0 0 30 44"><path d="M8 4l16 18L8 40" stroke="#fff" stroke-width="4" fill="none"/></svg>
  <div class="abs avatar" role="img" aria-label="Client portrait"></div>
  <span class="quote-mark" style="left:278px;top:110px">&ldquo;</span>
  <blockquote>Lorem ipsum dolor sit amet, consectetur adipiscing elit, sed do eiusmod tempor incididunt ut labore et dolore magna aliqua. Ut enim ad minim veniam, quis nostrud exercitation ullamco laboris nisi ut aliquip ex ea commodo consequat.</blockquote>
  <span class="quote-mark" style="left:594px;top:196px">&rdquo;</span>
  <div class="who"><b>Jordan Avery</b><span>Company Name</span></div>
</section>

<footer class="abs site-footer">
  <div class="brand"><span class="brand-dot"></span><span class="brand-name">Tidewell<br>Homecare</span></div>
  <div class="socials"><span></span><span></span><span></span><span></span><span></span></div>
  <div class="vline" style="left:400px"></div>
  <div class="vline" style="left:748px"></div>
  <h4 style="left:471px">CONTACT US</h4>
  <div class="contact-row" style="top:158px"><svg viewBox="0 0 16 16"><path d="M8 1a5 5 0 015 5c0 4-5 9-5 9S3 10 3 6a5 5 0 015-5z" fill="#fff"/><circle cx="8" cy="6" r="2" fill="#1e1f21"/></svg><span>48 Harbor Lane, Bayview,<br>Coast County, USA.</span></div>
  <div class="contact-row" style="top:217px"><svg viewBox="0 0 24 24"><path fill="#fff" d="M6.6 10.8a15 15 0 006.6 6.6l2.2-2.2c.3-.3.7-.4 1-.2 1.1.4 2.3.6 3.6.6.6 0 1 .4 1 1V20c0 .6-.4 1-1 1A17 17 0 013 4c0-.6.4-1 1-1h3.5c.6 0 1 .4 1 1 0 1.3.2 2.5.6 3.6.1.3 0 .7-.2 1z"/></svg><span>(+1) 555 019 4410</span></div>
  <div class="contact-row" style="top:259px"><svg viewBox="0 0 16 16"><rect x="1" y="3" width="14" height="10" fill="#fff"/><path d="M1 3l7 6 7-6" stroke="#1e1f21" fill="none"/></svg><span>hello@tidewellhomecare.example</span></div>
  <h4 style="left:817px">NEWSLETTER SUBSCRIPTION</h4>
  <p class="news-text">Register your Email Address to get a more Information about us</p>
  <div class="news-input">Email</div>
  <div class="news-btn">SUBSCRIBE</div>
  <div class="footer-rule"></div>
  <p class="copyright">Copyrights © 2020 Tidewell Homecare.&nbsp; All Rights Reserved &nbsp;&nbsp;&nbsp;&nbsp;|&nbsp;&nbsp;&nbsp;&nbsp; Privacy Policy.</p>
</footer>

</body>
</html>
```